Harborline Auto LLC

Car Dealer Customer Service
Address: 2874 Cresthaven Road, Shelbyville, TN 37162
web: www.harborlineautoxq.net
email: harborlineautoxq@mailnest.example
Phone: (931) 555-0148
Phone: (629) 555-0173

```html
<!DOCTYPE html>
<html lang="en">
<head>
<meta charset="utf-8">
<title>Harborline Auto – Business Card</title>
<link href="https://fonts.googleapis.com/css2?family=Montserrat:wght@400;500;800&display=swap" rel="stylesheet">
<style>
  :root{
    --stage:#3a3c40;
    --brand-blue:#1e7bad;
    --band-blue:#2a8fc8;
    --brand-gold:#ebb140;
    --paper:#ffffff;
    --ink:#1c1c1c;
  }
  *{margin:0;padding:0;box-sizing:border-box}
  html,body{width:1200px;height:887px;overflow:hidden}
  body{background:var(--stage);font-family:"Montserrat",sans-serif;position:relative}
  .card{position:absolute;width:520px;height:300px;border-radius:26px;overflow:hidden;box-shadow:0 14px 30px rgba(0,0,0,.45)}
  .card--front{left:90px;top:80px;background:var(--brand-blue)}
  .card--back{left:590px;top:480px;background:var(--paper)}

  .brand{position:absolute;display:flex;align-items:center;gap:16px}
  .brand__dot{border-radius:50%;flex:none}
  .brand__name{font-weight:800;letter-spacing:1px;text-transform:uppercase;line-height:1;white-space:nowrap}
  .card--front .brand{left:50%;top:50%;transform:translate(-50%,-50%)}
  .card--front .brand__dot{width:64px;height:64px;background:var(--brand-gold)}
  .card--front .brand__name{color:var(--paper);font-size:30px}

  .card--back .brand{left:18px;width:220px;top:92px;flex-direction:column;align-items:center;gap:12px}
  .card--back .brand__dot{width:60px;height:60px;background:var(--brand-gold)}
  .card--back .brand__name{color:var(--brand-blue);font-size:18px;letter-spacing:.5px}

  .divider{position:absolute;left:248px;top:70px;width:1.5px;height:120px;background:var(--brand-blue)}
  .contacts{position:absolute;left:262px;right:12px;top:78px;list-style:none;font-size:12px;color:var(--ink)}
  .contacts li{display:flex;align-items:center;gap:7px;height:26px;white-space:nowrap}
  .contacts svg{width:13px;height:13px;fill:var(--brand-blue);flex:none}
  .contacts .accent{color:var(--band-blue)}

  .band{position:absolute;top:238px;height:34px;display:flex;align-items:center;color:var(--paper);white-space:nowrap}
  .band--address{left:0;width:330px;background:var(--band-blue);padding-left:18px;font-size:12px;clip-path:polygon(0 0,100% 0,96% 100%,0 100%)}
  .band--service{left:332px;right:0;background:var(--brand-gold);padding-left:14px;font-size:11px;clip-path:polygon(5% 0,100% 0,100% 100%,0 100%)}
</style>
</head>
<body>
  <section class="card card--front" aria-label="Card front">
    <div class="brand">
      <span class="brand__dot"></span>
      <span class="brand__name">Harborline Auto</span>
    </div>
  </section>

  <section class="card card--back" aria-label="Card back">
    <div class="brand">
      <span class="brand__dot"></span>
      <span class="brand__name">Harborline Auto</span>
    </div>
    <span class="divider"></span>
    <ul class="contacts">
      <li><svg viewBox="0 0 24 24"><path d="M6.6 10.8a15 15 0 006.6 6.6l2.2-2.2a1 1 0 011-.25 11.4 11.4 0 003.6.57 1 1 0 011 1V20a1 1 0 01-1 1A17 17 0 013 4a1 1 0 011-1h3.5a1 1 0 011 1c0 1.25.2 2.45.57 3.6a1 1 0 01-.25 1z"/></svg><span>(931) 555-0148</span></li>
      <li><svg viewBox="0 0 24 24"><path d="M6.6 10.8a15 15 0 006.6 6.6l2.2-2.2a1 1 0 011-.25 11.4 11.4 0 003.6.57 1 1 0 011 1V20a1 1 0 01-1 1A17 17 0 013 4a1 1 0 011-1h3.5a1 1 0 011 1c0 1.25.2 2.45.57 3.6a1 1 0 01-.25 1z"/></svg><span>(629) 555-0173</span></li>
      <li><svg viewBox="0 0 24 24"><path d="M2 5h20v14H2z M2 5l10 8 10-8" stroke="#fff" stroke-width="1.2"/></svg><span>harborlineautoxq@mailnest.example</span></li>
      <li><svg viewBox="0 0 24 24"><circle cx="12" cy="12" r="10"/></svg><span>www.<span class="accent">harborlineautoxq</span>.net</span></li>
    </ul>
    <div class="band band--address">2874 Cresthaven Road, Shelbyville, TN 37162</div>
    <div class="band band--service">Car Dealer Customer Service</div>
  </section>
</body>
</html>
```